Flyer for spiritual retreat (yoga, meditation, reiki, raw food)

I would like a flyer to promote my upcoming retreat and a matching Facebook banner.

The name of the retreat is "OutBloom the Spirit" and the tagline is "retreat into you"

The activities in the retreat include daily meditation, ecstatic dance, spiritual development workshops on intuition, energy healing etc and a reiki session is included.

I would like a flyer designed to promote this, something that is editable as I will be running this multiple times and will need to adjust the flyer to add the dates etc each time.

edit: add that here will be fully catered raw food and juices, and that the retreat price includes all accomodation, meals and workshops.

Please contact me if you need further info. Please also visit my website www.marlavosk.com and www.pagenest.com/koruhaven to see my current events and promotions.

Thank you,

Marla

Reason: Hi all, thank you all for your submissions. Apologies as I am traveling and do not have much access to internet and will review your submissions and provide feedback as soon as possible. Kind regards, Marla.

Target Market(s)

People who like meditation, yoga, fans of tomas brenner and wendell marsh, those interested in personal and spiritual development.

Industry/Entity Type

Health And Wellness

Requirements
Must have
• Please put the included reiki session as as added bonus. Something like "BONUS 30 minute reiki healing session" in a little star/banner/something that stands out.
• Please emphasise the "light" part of OutBloom as I am going for a play on words between in the light and enlightenment.
• Please include placeholder text for place, location, time
• Placeholder for price
• My name (see attached file - can change colour to suit) and website (www.marlavosk.com)
Nice to have
• I prefer rounded designs, curves rather than block designs.
Should not have
• Koru Haven logo

```html
<!DOCTYPE html>
<html lang="en">
<head>
<meta charset="utf-8">
<title>OutBloom the Spirit – Retreat Flyer</title>
<link rel="stylesheet" href="https://fonts.googleapis.com/css2?family=Asap:ital,wght@0,400;0,500;0,600;0,700;1,600&family=Great+Vibes&family=Lobster+Two:ital,wght@1,700&family=Open+Sans:wght@300;400&display=swap">
<style>
  :root {
    --stage: #2b2b2d;
    --sky: #eef2f4;
    --sea: #8fa9b8;
    --foliage: #4f6a3a;
    --earth: #6e5636;
    --earth-dark: #3c3322;
    --blue: #1f8fe3;
    --blue-light: #45b2f5;
    --blue-pale: #bfe0f5;
    --purple: #4b3f8e;
    --purple-deep: #3a2f78;
    --navy: #1d2b55;
    --white: #ffffff;
    --ink: #2a2a2a;
  }
  * { margin: 0; padding: 0; box-sizing: border-box; }
  html, body { width: 1200px; height: 787px; overflow: hidden; background: var(--stage); }
  .canvas { position: relative; width: 1200px; height: 787px; }

  .flyer {
    position: absolute; left: 336px; top: 18px;
    width: 640px; height: 910px;
    transform: scale(0.825); transform-origin: 0 0;
    overflow: hidden;
    font-family: "Asap", sans-serif;
    color: var(--white);
  }

  .photo-backdrop {
    position: absolute; inset: 0;
    background: linear-gradient(180deg,
      var(--sky) 0%, var(--sky) 11%, #cfdbe2 15%, var(--sea) 19%,
      #6f8a5a 26%, var(--foliage) 34%, #6a5a3c 45%, var(--earth) 55%,
      #5a5533 68%, #45512d 80%, var(--earth-dark) 100%);
  }
  .photo-portrait {
    position: absolute; left: 40px; top: 120px; width: 200px; height: 210px;
    border-radius: 50% 50% 40% 40%;
    background: radial-gradient(ellipse at 50% 45%, rgba(120,90,70,.55), rgba(60,50,40,0) 70%);
  }
  .photo-figure {
    position: absolute; left: 90px; top: 580px; width: 200px; height: 290px;
    background: radial-gradient(ellipse at 50% 50%, rgba(30,28,26,.55), rgba(30,28,26,0) 70%);
  }

  .signature {
    position: absolute; left: 90px; top: 8px;
    font-family: "Great Vibes", cursive; font-size: 70px; color: #3a3a3a;
  }

  .wave { position: absolute; left: 0; top: 0; width: 640px; height: 910px; }

  .bonus-badge {
    position: absolute; left: 192px; top: 254px; width: 122px; height: 122px;
    border-radius: 50%; background: var(--purple);
    border: 5px solid var(--blue-pale);
    display: flex; flex-direction: column; align-items: center; justify-content: center;
    text-align: center; line-height: 1.05;
  }
  .bonus-badge .bonus-label { font-size: 23px; font-weight: 600; }
  .bonus-badge .bonus-time { font-size: 16px; }
  .bonus-badge .bonus-reiki { font-size: 15px; color: var(--blue-light); font-weight: 500; }
  .bonus-badge .bonus-session { font-size: 21px; }

  .retreat-title {
    position: absolute; left: 340px; top: 248px; width: 290px; text-align: center;
  }
  .retreat-title .title-line { display: block; line-height: 1; }
  .retreat-title .title-lead { font-family: "Asap", sans-serif; font-weight: 600; font-size: 50px; }
  .retreat-title .title-light { font-family: "Lobster Two", cursive; font-style: italic; font-weight: 700; font-size: 66px; }
  .retreat-title .title-second { font-family: "Lobster Two", cursive; font-style: italic; font-weight: 700; font-size: 46px; margin-top: 2px; }
  .retreat-title .tagline {
    font-family: "Open Sans", sans-serif; font-weight: 300; font-size: 19px;
    letter-spacing: 1.5px; color: var(--navy); margin-top: 8px;
  }

  .activities-label {
    position: absolute; left: 44px; top: 390px; padding: 4px 10px;
    background: var(--purple); border-radius: 6px;
    font-size: 31px; font-weight: 500;
  }
  .activity-list { position: absolute; left: 50px; top: 446px; list-style: none; }
  .activity-list li {
    display: flex; align-items: center; height: 33.5px;
    font-size: 20px; font-weight: 500; text-shadow: 0 1px 3px rgba(0,0,0,.6);
  }
  .activity-list svg { width: 18px; height: 18px; margin-right: 14px; }

  .event-details {
    position: absolute; left: 318px; top: 588px; width: 320px; text-align: center;
    text-shadow: 0 1px 3px rgba(0,0,0,.6);
  }
  .event-details .icon { display: block; margin: 0 auto; width: 26px; height: 26px; }
  .event-details .date { font-size: 27px; font-weight: 600; margin: 2px 0 16px; }
  .event-details .time { font-size: 28px; font-weight: 600; margin-top: 2px; }
  .event-details .time em { font-style: italic; }
  .event-details .price { margin-top: 10px; line-height: 1; }
  .event-details .price-label { font-size: 31px; font-style: italic; font-weight: 600; }
  .event-details .price-amount { font-size: 44px; font-weight: 700; }
  .event-details .price-note { font-size: 12px; margin-top: 6px; }
  .event-details .visit { font-size: 16px; font-weight: 500; margin-top: 24px; }

  .contact-bar {
    position: absolute; left: 0; bottom: 0; width: 640px; height: 46px;
    background: rgba(70,60,130,.82);
    display: flex; align-items: center; justify-content: space-between; padding: 0 26px 0 40px;
  }
  .contact-bar .contact { display: flex; align-items: center; }
  .contact-bar .dot { width: 14px; height: 14px; border-radius: 50%; background: var(--white); margin-right: 10px; }
  .contact-bar .social { font-size: 13px; font-weight: 500; }
  .contact-bar .website { font-size: 23px; }
  .contact-bar .website .dot { width: 16px; height: 16px; margin-right: 14px; }
</style>
</head>
<body>
<main class="canvas">
  <article class="flyer">
    <div class="photo-backdrop" role="img" aria-label="Photograph of a coastal cliff with sea, trees and rocky hillside"></div>
    <div class="photo-portrait" role="img" aria-label="Portrait photograph of the retreat host"></div>
    <div class="photo-figure" role="img" aria-label="Photograph of the host seated by a wooden railing in nature"></div>

    <div class="signature">Marla Vosk</div>

    <svg class="wave" viewBox="0 0 640 910" aria-hidden="true">
      <defs>
        <radialGradient id="blueGlow" cx="0.45" cy="0.4" r="0.7">
          <stop offset="0" stop-color="#4cb6f6"/>
          <stop offset="1" stop-color="#1683dc"/>
        </radialGradient>
      </defs>
      <path d="M0,252 C90,300 170,320 250,310 C360,295 440,230 640,175 L640,480 C560,470 470,470 400,440 C330,410 270,420 230,430 C150,440 70,380 0,360 Z" fill="rgba(255,255,255,.35)"/>
      <path d="M0,262 C90,300 170,310 240,300 C340,285 450,205 640,185 L640,448 C570,455 480,440 400,410 C330,385 270,390 200,400 C130,395 60,360 0,348 Z" fill="rgba(190,224,245,.45)"/>
      <path d="M300,285 C380,235 480,200 640,190 L640,440 C560,445 470,420 400,395 C350,378 320,370 300,372 Z" fill="url(#blueGlow)"/>
    </svg>

    <div class="bonus-badge">
      <span class="bonus-label">BONUS</span>
      <span class="bonus-time">30 minute</span>
      <span class="bonus-reiki">reiki healing</span>
      <span class="bonus-session">session</span>
    </div>

    <h1 class="retreat-title">
      <span class="title-line"><span class="title-lead">Out</span><span class="title-light">Bloom</span></span>
      <span class="title-line title-second">the Spirit</span>
      <span class="title-line tagline">RETREAT INTO YOU</span>
    </h1>

    <h2 class="activities-label">The activities</h2>
    <ul class="activity-list">
      <li><svg viewBox="0 0 18 18"><path d="M2 10 L7 15 L16 3" fill="none" stroke="#fff" stroke-width="2.4" stroke-linecap="round"/></svg>daily meditation,</li>
      <li><svg viewBox="0 0 18 18"><path d="M2 10 L7 15 L16 3" fill="none" stroke="#fff" stroke-width="2.4" stroke-linecap="round"/></svg>ecstatic dance,</li>
      <li><svg viewBox="0 0 18 18"><path d="M2 10 L7 15 L16 3" fill="none" stroke="#fff" stroke-width="2.4" stroke-linecap="round"/></svg>spiritual development workshops on intuition,</li>
      <li><svg viewBox="0 0 18 18"><path d="M2 10 L7 15 L16 3" fill="none" stroke="#fff" stroke-width="2.4" stroke-linecap="round"/></svg>energy healing etc</li>
    </ul>

    <section class="event-details">
      <svg class="icon" viewBox="0 0 26 26"><rect x="2" y="4" width="22" height="19" rx="2" fill="none" stroke="#fff" stroke-width="2"/><rect x="2" y="4" width="22" height="5" fill="#fff"/><g fill="#fff"><rect x="6" y="12" width="3" height="3"/><rect x="11.5" y="12" width="3" height="3"/><rect x="17" y="12" width="3" height="3"/><rect x="6" y="17" width="3" height="3"/><rect x="11.5" y="17" width="3" height="3"/></g></svg>
      <p class="date">1st january,2017</p>
      <svg class="icon" viewBox="0 0 26 26"><circle cx="13" cy="13" r="11" fill="none" stroke="#fff" stroke-width="2.2"/><path d="M13 7 V13 L8 16" fill="none" stroke="#fff" stroke-width="2.2" stroke-linecap="round"/></svg>
      <p class="time">4 pm <em>onward</em></p>
      <p class="price"><span class="price-label">Cost</span> <span class="price-amount">$150</span></p>
      <p class="price-note">(includes all accomodation, meals and workshops.)</p>
      <p class="visit">For more please also visit my website</p>
    </section>

    <footer class="contact-bar">
      <span class="contact social"><span class="dot"></span>www.pagenest.com/koruhaven</span>
      <span class="contact website"><span class="dot"></span>www.marlavosk.com</span>
    </footer>
  </article>
</main>
</body>
</html>
```